Bright Towns Forum PowerPoint Design Template and Sample Deck

The Bright Towns Forum is an international organization that seeks to improve the livability, workability and sustainability of the world’s cities.
We seek a versatile PowerPoint design template with 10 slide types plus a “self-documenting” sample deck. Your design will be used in keynote speeches and workshops around the world.
After the contest is completed, we will ask the winning designer to add 10-20 additional slide types for $75 per slide. We also seek a long-term relationship whereby we can request “custom” slides and/or ask the designer to touch up the slides we build to make them better.
FILES. We have uploaded several files:
2. PALETTE. Shows our official colors.
3 LOGOS. Several individual files with different variations of our logo. Some with our motto, some without.
2. SAMPLE SLIDES. Because we were unable to successfully upload our sample deck, we are making it available via this FileNook link:
https://www.filenook-example.com/s/k7qrtmzp2wd9hxa/The%20Bright%20Towns%20Forum%20Design%20Contest%20Notes.docx?dl=0
Target Market(s)
Mayors, department heads, CIOs, senior executives from technology companies
Industry/Entity Type
Information Technology
Colors
Designer to choose colors to be used in the design.
Requirements
Must have
- Please see uploaded Word document for requirements, nice to haves and should not haves and uploaded palette for color preferences.
Nice to have
- see above
Should not have
- see above

```html
<!DOCTYPE html>
<html lang="en">
<head>
<meta charset="utf-8">
<title>Lorem Ipsum</title>
<link rel="stylesheet" href="https://fonts.googleapis.com/css2?family=Open+Sans:wght@400;700&display=swap">
<style>
  :root {
    --brand-blue: #00468b;
    --navy: #0c2f5c;
    --ink: #1a1a1a;
    --white: #ffffff;
    --photo-dark: #1c2530;
    --photo-mid: #3a4350;
  }
  * { margin: 0; padding: 0; box-sizing: border-box; }
  html, body { width: 1200px; height: 675px; overflow: hidden; background: var(--white); }
  .slide {
    position: relative; width: 1200px; height: 675px; overflow: hidden;
    font-family: "Open Sans", Arial, sans-serif; background: var(--white);
  }
  .hero-photo {
    position: absolute; left: 0; top: 0; width: 555px; height: 675px;
    background:
      radial-gradient(ellipse at 65% 30%, #5a5350 0%, transparent 55%),
      radial-gradient(ellipse at 30% 85%, #55575c 0%, transparent 50%),
      linear-gradient(135deg, var(--photo-mid) 0%, var(--photo-dark) 100%);
  }
  .hero-title {
    position: absolute; left: 61px; top: 310px;
    color: var(--white); font-weight: 700; font-size: 47px; letter-spacing: 0.5px;
  }
  .feature-list { list-style: none; }
  .feature {
    position: absolute; left: 0; width: 1200px; height: 94px;
  }
  .feature-badge {
    position: absolute; left: 502px; top: 0; width: 94px; height: 94px;
    border-radius: 50%; background: var(--white);
    display: flex; align-items: center; justify-content: center;
  }
  .feature-badge .disc {
    width: 84px; height: 84px; border-radius: 50%; background: var(--brand-blue);
    display: flex; align-items: center; justify-content: center; color: var(--white);
  }
  .feature-badge svg { width: 46px; height: 46px; }
  .rupee { font-size: 50px; font-weight: 400; line-height: 1; }
  .feature-text {
    position: absolute; left: 626px; top: 22px; width: 440px;
    font-size: 17px; line-height: 24px; color: var(--ink); text-align: justify;
  }
  .feature-text strong { color: #1f4e8c; font-weight: 700; }
  .page-number {
    position: absolute; left: 1089px; top: 622px; width: 51px; height: 51px;
    border-radius: 50%; background: var(--navy); color: var(--white);
    font-size: 14px; display: flex; align-items: center; justify-content: center;
  }
</style>
</head>
<body>
<main class="slide">
  <div class="hero-photo" role="img" aria-label="Photo of two business colleagues reviewing a tablet together"></div>
  <h1 class="hero-title">LOREM IPSUM</h1>

  <ul class="feature-list">
    <li class="feature" style="top:41px">
      <div class="feature-badge"><div class="disc">
        <svg viewBox="0 0 48 48" fill="none" stroke="currentColor" stroke-width="2.5">
          <rect x="7" y="9" width="34" height="24" rx="1.5"/>
          <line x1="5" y1="38" x2="43" y2="38"/>
          <g stroke-width="2.2"><line x1="24" y1="14" x2="24" y2="28"/><line x1="17" y1="21" x2="31" y2="21"/><line x1="19" y1="16" x2="29" y2="26"/><line x1="29" y1="16" x2="19" y2="26"/></g>
        </svg>
      </div></div>
      <p class="feature-text"><strong>Lorem Ipsum</strong> is simply dummy text of the printing and typesetting industry.</p>
    </li>
    <li class="feature" style="top:161px">
      <div class="feature-badge"><div class="disc">
        <svg viewBox="0 0 48 48" fill="none" stroke="currentColor" stroke-width="2.5">
          <rect x="10" y="8" width="22" height="32" rx="2"/>
          <rect x="16" y="5" width="10" height="6" rx="1" fill="currentColor"/>
          <rect x="14" y="17" width="4" height="4"/><rect x="14" y="25" width="4" height="4"/><rect x="14" y="33" width="4" height="3"/>
          <circle cx="34" cy="30" r="9" fill="currentColor"/>
          <polyline points="29.5,30 33,33.5 38.5,26.5" stroke="#00468b" stroke-width="3"/>
        </svg>
      </div></div>
      <p class="feature-text"><strong>Lorem Ipsum</strong> is simply dummy text of the printing and typesetting industry.</p>
    </li>
    <li class="feature" style="top:281px">
      <div class="feature-badge"><div class="disc">
        <svg viewBox="0 0 48 48" fill="currentColor">
          <path d="M6 12 L12 8 L27 32 L21 36 Z"/>
          <path d="M21 36 L27 32 L26 40 Z"/>
          <ellipse cx="32" cy="24" rx="12" ry="9"/>
          <polyline points="26,23 31,29 39,18" fill="none" stroke="#00468b" stroke-width="3"/>
        </svg>
      </div></div>
      <p class="feature-text"><strong>Lorem Ipsum</strong> is simply dummy text of the printing and typesetting industry.</p>
    </li>
    <li class="feature" style="top:401px">
      <div class="feature-badge"><div class="disc">
        <svg viewBox="0 0 48 48" fill="currentColor">
          <circle cx="26" cy="11" r="5.5"/>
          <path d="M17 20 Q26 16 34 20 L34 44 L19 44 Z"/>
        </svg>
      </div></div>
      <p class="feature-text"><strong>Lorem Ipsum</strong> is simply dummy text of the printing and typesetting industry.</p>
    </li>
    <li class="feature" style="top:521px">
      <div class="feature-badge"><div class="disc"><span class="rupee">₹</span></div></div>
      <p class="feature-text"><strong>Lorem Ipsum</strong> is simply dummy text of the printing and typesetting industry.</p>
    </li>
  </ul>

  <div class="page-number">4</div>
</main>
</body>
</html>
```